Mobile app for checking bus arrival

I would like to make the UI much more beautiful and modern. The app is an app to check bus arrival in Singapore.
See here: https://apps.veltrano.com/store/apps/details?id=com.ridoka&hl=en

Based on the question from designers:

1. The first screen shows the favorite bus stop. Each item shows location / street, the top one is the location, second line is the street name. And the number is the bus stop code.

2. Please download the app and try bus stop code with 07589 or 10079, for example. It will bring you to the next screen.

3. The pencil allow you to select color theme, for the list item, and the header.

4. On the second screen, it will show up the list of bus route that available on that bus stop.

5. When you tap on one of them it will show you the 2 subsequent arrival time.

6. Each of the arrival time has the information of availability seats available, seats not available, no more space. (we can use green, yellow, red, respectively).

7. Each of the arrival time has the WAB indicator (Wheelchair availability). Show as icon is preferred.

7. KLT and VOPN are the bus provider in Singapore. 48 means the route /service no.

Requirements:
And check the attachment, see screen 3. I need to add information about the space availability, which has 3 state: seats available, seats not available, no more space. (we can use green, yellow, red, respectively).

Please advise how to show the information.

Target Market(s)

Students, age below 35

Industry/Entity Type

Trivex

Requirements
Must have
• The app currently has the capabilities to select color theme, checkout screen1. It's the button and the list item color.
Nice to have
• Please download the app to see all available colors, and make suggestion to have better color pallete.

```html
<!DOCTYPE html>
<html lang="en">
<head>
<meta charset="utf-8">
<title>Bus Stop 07589 – Arrivals</title>
<link href="https://fonts.googleapis.com/css2?family=Roboto:wght@300;400;500&display=swap" rel="stylesheet">
<style>
  :root {
    --page-bg: #e4e4e4;
    --status-bar: #4a2a82;
    --app-bar: #673ab7;
    --on-primary: #ffffff;
    --stop-title: #6a3bbf;
    --surface: #ffffff;
    --body-bg: #f0f3f6;
    --service-number: #555a5e;
    --operator-klt: #e53935;
    --operator-vopn: #5468f0;
    --favourite: #f9a825;
    --divider: #ddd3ee;
  }
  * { box-sizing: border-box; margin: 0; padding: 0; }
  html, body {
    width: 960px; height: 1200px; overflow: hidden;
    background: var(--page-bg);
    font-family: "Roboto", Arial, sans-serif;
  }
  .screen {
    position: absolute; left: 141px; top: 0;
    width: 677px; height: 1200px;
    background: var(--body-bg);
    overflow: hidden;
  }
  .status-bar {
    height: 46px; background: var(--status-bar);
    display: flex; align-items: center; justify-content: flex-end;
    gap: 12px; padding-right: 18px;
    color: var(--on-primary); font-size: 24px;
  }
  .app-bar {
    height: 104px; background: var(--app-bar);
    position: relative; color: var(--on-primary);
  }
  .app-bar .back { position: absolute; left: 40px; top: 37px; }
  .app-bar .stop-code {
    position: absolute; left: 92px; top: 30px;
    font-size: 38px; font-weight: 400; letter-spacing: 0.5px;
  }
  .app-bar .refresh { position: absolute; left: 546px; top: 34px; }
  .app-bar .menu { position: absolute; left: 624px; top: 35px; }
  .stop-header {
    position: relative; height: 154px; background: var(--surface);
    border-bottom: 3px solid var(--divider);
    box-shadow: 0 2px 4px rgba(0,0,0,0.08);
  }
  .stop-name {
    position: absolute; left: 34px; top: 32px;
    font-size: 37px; font-weight: 500; color: var(--stop-title);
  }
  .stop-street {
    position: absolute; left: 34px; top: 96px;
    font-size: 22px; color: var(--stop-title);
  }
  .favourite { position: absolute; left: 585px; top: 50px; }
  .service-grid {
    display: grid; grid-template-columns: 311px 311px;
    column-gap: 17px; row-gap: 15px;
    padding: 24px 19px 0 19px;
  }
  .service-tile {
    position: relative; height: 150px; background: var(--surface);
    box-shadow: 0 1px 3px rgba(0,0,0,0.12);
  }
  .operator {
    position: absolute; left: 12px; top: 10px;
    font-size: 20px; font-weight: 400;
  }
  .operator.klt { color: var(--operator-klt); }
  .operator.vopn { color: var(--operator-vopn); }
  .service-number {
    position: absolute; left: 0; right: 0; top: 46px;
    text-align: center; font-size: 64px; font-weight: 300;
    color: var(--service-number);
  }
</style>
</head>
<body>
<main class="screen">
  <div class="status-bar">
    <svg width="24" height="24" viewBox="0 0 24 24" aria-hidden="true"><path d="M2 22 L22 22 L22 2 Z" fill="#ffffff" opacity="0.55"/><path d="M10 22 L22 22 L22 10 Z" fill="#ffffff"/></svg>
    <svg width="16" height="26" viewBox="0 0 16 26" aria-hidden="true"><rect x="5" y="0" width="6" height="3" fill="#ffffff" opacity="0.55"/><rect x="0" y="3" width="16" height="23" rx="1" fill="#ffffff" opacity="0.55"/><rect x="0" y="13" width="16" height="13" rx="1" fill="#ffffff"/></svg>
    <span class="clock">12:30</span>
  </div>

  <header class="app-bar">
    <svg class="back" width="30" height="30" viewBox="0 0 30 30" aria-label="Back"><path d="M20 4 L9 15 L20 26" fill="none" stroke="#ffffff" stroke-width="3.2" stroke-linecap="round" stroke-linejoin="round"/></svg>
    <h1 class="stop-code">07589</h1>
    <svg class="refresh" width="38" height="38" viewBox="0 0 38 38" aria-label="Refresh"><path d="M30 12 A13 13 0 1 0 32 22" fill="none" stroke="#ffffff" stroke-width="3.6" stroke-linecap="round"/><path d="M23 11 L32 11 L32 2" fill="none" stroke="#ffffff" stroke-width="3.6" stroke-linecap="round" stroke-linejoin="round"/></svg>
    <svg class="menu" width="10" height="34" viewBox="0 0 10 34" aria-label="More options"><circle cx="5" cy="4" r="3.8" fill="#ffffff"/><circle cx="5" cy="17" r="3.8" fill="#ffffff"/><circle cx="5" cy="30" r="3.8" fill="#ffffff"/></svg>
  </header>

  <section class="stop-header">
    <h2 class="stop-name">Opp Varden Ctr</h2>
    <p class="stop-street">Lunet Rd</p>
    <svg class="favourite" width="56" height="54" viewBox="0 0 24 23" aria-label="Favourite"><path d="M12 0.8 L15.1 8.1 L23 8.7 L17 13.9 L18.8 21.6 L12 17.5 L5.2 21.6 L7 13.9 L1 8.7 L8.9 8.1 Z" fill="var(--favourite)"/></svg>
  </section>

  <section class="service-grid">
    <div class="service-tile"><span class="operator klt">KLT</span><span class="service-number">48</span></div>
    <div class="service-tile"><span class="operator klt">KLT</span><span class="service-number">57</span></div>
    <div class="service-tile"><span class="operator klt">KLT</span><span class="service-number">130</span></div>
    <div class="service-tile"><span class="operator vopn">VOPN</span><span class="service-number">851</span></div>
    <div class="service-tile"><span class="operator vopn">VOPN</span><span class="service-number">960</span></div>
    <div class="service-tile"><span class="operator klt">KLT</span><span class="service-number">2N</span></div>
    <div class="service-tile"><span class="operator klt">KLT</span><span class="service-number">4N</span></div>
  </section>
</main>
</body>
</html>
```